A paperback book cover entitled: The Keystone

1. For the front cover of the paperback I need the photo of me walking down the driveway at Wexcombe Hall as the focal point. The designer will use their discretion where to insert the book title: The Keystone.
Also the designer will use their discretion where my name Desmond Harrowby as the author is placed. Attached is a contemporary photo of me to use if the designer thinks that possible. Both these photos are attached.
2. The back cover page will contain two main written insertions (1) About the Book and (2) About the Author.
The book will be an 8.5x11 inch paperback of some 570 pages published by Brindlepress.
About the book:
This book is about Australian Public Affairs 1957-2020 as perceived and observed by Desmond Harrowby. It has a significant but not exclusive Queensland focus concerning History, Commentary, and Anecdotes, plus some things Desmond has been involved with along the way.
Desmond developed unique Transition to Government and Transition to Opposition plans that have all been implemented. Some of those plans are referred to in the book and other Transition plans are appendixes to the book.
Now at 73 years of age, Desmond’s motivation for writing this book is to ensure a wealth of historical scenarios are captured and incorporated into the public record for future generations.

About the author:

Desmond Harrowby has been a largely silent and invisible political confidant to Australian Premiers and Prime Ministers.
Desmond worked in the Queensland public sector from 1971-2009 as Chief of Staff to four Queensland State Opposition Leaders for 13 years and then as a Public Sector senior executive.
He subsequently served on the Edith Tarrant Foundation Board, the Orrin Vale Records Hall Board, and consulted to a mining company. He has recorded many Oral History projects for The Fernwick Archive in Canberra.
Over the last 30+ years, he has been approached countless times for advice relating to Business, Government, Authors, Historians, and people seeking a job. He has never charged a cent for any of his advice, even when not working within Government.
There are two extra photos attached to maybe be on each side at the bottom of the back cover if the designer thinks it is appropriate.
Those in the 4 person photo from the left were all connected with the Tallowmere Assembly: former Unity Minister Neil Corrigan, Former Heartland Party Premier Tom Beaulieu, former Progress Leader Glen Osborne, and Desmond Harrowby

In the three person photo from the left are: Desmond Harrowby, Former PM Rupert Danforth, and Prime Minister Brian Ferrow.

3. In the spine of the book will be simply (1) The Keystone and (2) Desmond Harrowby

Here’s hoping a good design is created.

```html
<!DOCTYPE html>
<html lang="en">
<head>
<meta charset="utf-8">
<title>The Keystone — Cover Spread</title>
<link rel="stylesheet" href="https://fonts.googleapis.com/css2?family=Playfair+Display:ital,wght@0,900;1,700&family=Libre+Baskerville:wght@700&family=Tinos&display=swap">
<style>
  :root {
    --stage: #d9d9d9;
    --paper-light: #ecd9b6;
    --paper-mid: #e0c497;
    --paper-edge: #c49a68;
    --ink: #1d1914;
    --frame: #2a231b;
    --photo-light: #b9b4ab;
    --photo-dark: #4a463f;
    --spine-line: rgba(90, 62, 30, 0.25);
  }
  * { box-sizing: border-box; margin: 0; padding: 0; }
  html, body { width: 800px; height: 1200px; overflow: hidden; background: var(--stage); }
  .canvas { position: relative; width: 800px; height: 1200px; }
  .spread {
    position: absolute; left: 20px; top: 372px; width: 760px; height: 456px;
    display: flex; box-shadow: 0 4px 14px rgba(0,0,0,0.18);
  }
  .panel {
    position: relative; height: 100%;
    background: radial-gradient(ellipse at 50% 45%, var(--paper-light) 0%, var(--paper-mid) 65%, var(--paper-edge) 100%);
  }
  .back-cover { width: 354px; }
  .spine { width: 52px; border-left: 1px solid var(--spine-line); border-right: 1px solid var(--spine-line); }
  .front-cover { width: 354px; }

  .title { position: absolute; left: 0; right: 0; text-align: center; font-family: "Playfair Display", Georgia, serif; font-weight: 900; color: var(--ink); line-height: 1; }
  .back-cover .title-the { top: 22px; font-size: 25px; }
  .back-cover .title-main { top: 44px; font-size: 34px; }
  .front-cover .title-the { top: 16px; font-size: 32px; }
  .front-cover .title-main { top: 47px; font-size: 46px; }

  .section-heading {
    position: absolute; left: 30px; font-family: "Playfair Display", Georgia, serif;
    font-style: italic; font-weight: 700; font-size: 13px; line-height: 1; color: var(--ink); letter-spacing: 0.5px;
  }
  .about-book-heading { top: 95px; }
  .about-author-heading { top: 181px; }
  .body-copy {
    position: absolute; font-family: "Tinos", "Times New Roman", serif;
    font-size: 5.9px; line-height: 1.22; color: var(--ink);
  }
  .body-copy p { margin-bottom: 2px; }
  .about-book-copy { left: 30px; top: 111px; width: 296px; }
  .about-author-copy { left: 30px; top: 198px; width: 300px; }
  .author-portrait {
    float: left; width: 64px; height: 64px; margin: 1px 6px 1px 0;
    background: linear-gradient(160deg, #5b6570 0%, #2c3440 100%);
    border: 1px solid var(--frame);
  }

  .snapshot { position: absolute; border: 2px solid var(--frame); }
  .snapshot-four { left: 56px; top: 302px; width: 110px; height: 76px; background: linear-gradient(180deg, #d6d2c8 0%, #8a8680 100%); }
  .snapshot-three { left: 176px; top: 302px; width: 120px; height: 76px; background: linear-gradient(180deg, #c7a868 0%, #4a3e2c 100%); }

  .spine-title, .spine-author {
    position: absolute; left: 0; right: 0; writing-mode: vertical-rl;
    display: flex; align-items: center; color: var(--ink); white-space: nowrap;
  }
  .spine-title { top: 62px; font-family: "Playfair Display", Georgia, serif; font-weight: 900; line-height: 1; }
  .spine-title .spine-the { font-size: 16px; }
  .spine-title .spine-main { font-size: 24px; }
  .spine-author { top: 272px; justify-content: center; font-family: "Libre Baskerville", Georgia, serif; font-weight: 700; font-size: 9.5px; letter-spacing: 1.5px; }

  .cover-photo {
    position: absolute; left: 57px; top: 101px; width: 230px; height: 309px;
    border: 4px solid var(--frame);
    background: linear-gradient(180deg, #8e8a82 0%, var(--photo-light) 45%, #a39e95 70%, var(--photo-dark) 100%);
  }
  .author-name {
    position: absolute; left: 0; right: 0; top: 421px; text-align: center; line-height: 1;
    font-family: "Libre Baskerville", Georgia, serif; font-weight: 700; font-size: 16px;
    letter-spacing: 1.8px; color: var(--ink);
  }
</style>
</head>
<body>
<main class="canvas">
  <section class="spread">
    <article class="panel back-cover">
      <div class="title title-the">THE</div>
      <div class="title title-main">KEYSTONE</div>

      <h2 class="section-heading about-book-heading">About the book:</h2>
      <div class="body-copy about-book-copy">
        <p>This book is about Australian Public Affairs 1957-2020 as perceived and observed by Desmond Harrowby. It has a significant but not exclusive Queensland focus concerning History, Commentary, and Anecdotes, plus some things Desmond has been involved with along the way.</p>
        <p>Desmond developed unique Transition to Government and Transition to Opposition plans that have all been implemented. Some of those plans are referred to in the book and other Transition plans are appendixes to the book. Now at 73 years of age, Desmond’s motivation for writing this book is to ensure a wealth of historical scenarios are captured and incorporated into the public record for future generations.</p>
      </div>

      <h2 class="section-heading about-author-heading">About the author:</h2>
      <div class="body-copy about-author-copy">
        <div class="author-portrait" role="img" aria-label="Contemporary portrait photo of Desmond Harrowby"></div>
        <p>Desmond Harrowby has been a largely silent and invisible political confidant to Australian Premiers and Prime Ministers.</p>
        <p>Desmond worked in the Queensland public sector from 1971-2009 as Chief of Staff to four Queensland State Opposition Leaders for 13 years and then as a Public Sector senior executive.</p>
        <p>He subsequently served on the Edith Tarrant Foundation Board, the Orrin Vale Records Hall Board, and consulted to a mining company. He has recorded many Oral History projects for The Fernwick Archive in Canberra. Over the last 30+ years, he has been approached countless times for advice relating to Business, Government, Authors, Historians, and people seeking a job. He has never charged a cent for any of his advice, even when not working within Government.</p>
      </div>

      <div class="snapshot snapshot-four" role="img" aria-label="Photo of four men standing together in a dining room"></div>
      <div class="snapshot snapshot-three" role="img" aria-label="Photo of three men together in a warmly lit room"></div>
    </article>

    <aside class="panel spine">
      <div class="spine-title"><span class="spine-the">THE</span><span class="spine-main">KEYSTONE</span></div>
      <div class="spine-author">Desmond Harrowby</div>
    </aside>

    <article class="panel front-cover">
      <h1 class="title title-the">THE</h1>
      <div class="title title-main">KEYSTONE</div>
      <div class="cover-photo" role="img" aria-label="Black and white photo of the young author walking down the driveway at Wexcombe Hall"></div>
      <div class="author-name">Desmond Harrowby</div>
    </article>
  </section>
</main>
</body>
</html>
```